Small butcher shop from Austria needs great powerpoint presentation

We are looking for a powerpoint template for our new CI - it should be modern and clear.

Logo (2 Versions), Slogan, Business Card and Car-Wrap-Design already exist. (See documents below.)

We won't use much text. About 50% of the presentation should be pictures, included in different ways.

We are a family business in Upper Austria, only process animals from farms in the immediate vicinity, produce the products by hand, value animal welfare and short transport routes and avoid packaging as much as possible.

The design should be modern and clear.

Sans Serif

• Use the red color sparingly. Only use sans serif fonts (Myriad Pro - if possible). The logo needs to be on first and last page only.

```html
<!DOCTYPE html>
<html lang="de">
<head>
<meta charset="utf-8">
<title>Halmer Fleischhauerei – Präsentation</title>
<link href="https://fonts.googleapis.com/css2?family=Source+Sans+3:wght@400;600;700;800&display=swap" rel="stylesheet">
<style>
  :root{
    --canvas:#1e1e1e;
    --maroon:#7a0f1e;
    --grey:#5f6062;
    --white:#ffffff;
    --ink:#333333;
    --rule:#8a8a8a;
  }
  *{box-sizing:border-box;margin:0;padding:0}
  html,body{width:1200px;height:4996px;overflow:hidden}
  body{background:var(--canvas);font-family:"Source Sans 3",sans-serif;color:var(--ink);position:relative}
  .slide{position:absolute;left:105px;width:1002px;height:558px;background:var(--white);overflow:hidden;border-bottom:4px solid var(--maroon)}
  .abs{position:absolute}
  .photo{position:absolute;display:block}
  .page-no{position:absolute;right:0;bottom:0;width:45px;height:36px;background:var(--maroon);color:var(--white);font-weight:700;font-size:14px;display:flex;align-items:center;justify-content:center}
  .heading{color:var(--maroon);font-weight:700;font-size:14px;line-height:1.4;text-transform:uppercase}
  .copy{font-size:11px;line-height:1.55;color:var(--ink)}
  .light .heading,.light .copy{color:var(--white)}
  .brand-name{color:var(--maroon);font-weight:700;font-size:72px;letter-spacing:4px;line-height:1}
  .brand-sub{color:var(--maroon);font-weight:600;font-size:11px;letter-spacing:3px;margin-top:4px}
</style>
</head>
<body>

<!-- Title -->
<section class="slide" style="top:122px;border-bottom:none">
  <div class="photo" role="img" aria-label="Holstein cow grazing in a sunny meadow with forest and sky" style="inset:0;background:linear-gradient(180deg,#a9c1d4 0%,#d9e1e2 30%,#6d8a46 48%,#7fa246 75%,#4f6d2a 100%)"></div>
  <div class="abs" style="left:0;right:0;top:92px;text-align:center">
    <div class="brand-name">HALMER</div>
    <div class="brand-sub">FLEISCHHAUEREI</div>
  </div>
  <div class="abs" style="left:745px;top:440px;color:var(--white);font-weight:800;line-height:1">
    <div style="font-size:30px;letter-spacing:1px">WELCOME TO</div>
    <div style="font-size:64px;letter-spacing:2px;margin-top:4px">HALMER</div>
  </div>
</section>

<!-- 01 -->
<section class="slide" style="top:725px">
  <div class="photo" role="img" aria-label="Two marbled raw rib-eye steaks on a dark background with herbs" style="inset:0;background:radial-gradient(ellipse at 30% 75%,#7c1d24 0%,#4d1015 35%,transparent 60%),radial-gradient(ellipse at 75% 70%,#8a2028 0%,#50121a 35%,transparent 60%),linear-gradient(180deg,#141414,#1f1515)"></div>
  <div class="abs" style="left:27px;top:88px;opacity:.75">
    <div class="brand-name" style="font-size:64px">HALMER</div>
    <div class="brand-sub">FLEISCHHAUEREI</div>
  </div>
  <div class="abs" style="left:0;right:0;top:40px;text-align:center;color:var(--white);font-weight:800;font-size:34px;letter-spacing:4px;line-height:1.25">WEIL REGIONALES<br>BESSER SCHMECKT</div>
  <div class="page-no">01</div>
</section>

<!-- 02 -->
<section class="slide" style="top:1326px">
  <div class="photo" role="img" aria-label="Butcher's hands holding raw steak beside a cleaver on a wooden board" style="left:0;top:0;width:502px;height:280px;background:linear-gradient(135deg,#3a2a22,#6b3b30 50%,#2a1e19)"></div>
  <div class="abs" style="left:553px;top:52px;width:400px">
    <div class="heading">Lorem ipsum is simply dummy text</div>
    <p class="copy" style="margin-top:10px">There are many variations of passages of Lorem Ipsum available, but the majority have suffered alteration in some form, by injected humour, or randomised words which don't look even slightly believable. If you are going to use a passage of Lorem Ipsum, you need to be sure there isn't anything embarrassing hidden in the middle of text. All the Lorem Ipsum generators on the Internet tend to repeat predefined chunks as necessary, making this the first true generator on the Internet.</p>
  </div>
  <div class="abs" style="left:56px;top:335px;width:390px">
    <div class="heading">Lorem ipsum is simply dummy text</div>
    <p class="copy" style="margin-top:10px">There are many variations of passages of Lorem Ipsum available, but the majority have suffered alteration in some form, by injected humour, or randomised words which don't look even slightly believable. If you are going to use a passage of Lorem Ipsum, you need to be sure there isn't anything embarrassing hidden in the middle of text. All the Lorem Ipsum generators on the Internet tend to repeat predefined chunks as necessary, making this the first true generator on the Internet.</p>
  </div>
  <div class="photo" role="img" aria-label="Holstein cow in front of a herd at a farm barn" style="left:502px;top:280px;width:500px;height:278px;background:linear-gradient(180deg,#d7dde2 0%,#b9bfc2 40%,#5a5046 70%,#3e3a33 100%)"></div>
  <div class="page-no">02</div>
</section>

<!-- 03 -->
<section class="slide" style="top:1929px">
  <div class="photo" role="img" aria-label="Raw steaks with garlic on a dark board" style="left:23px;top:33px;width:221px;height:328px;background:linear-gradient(160deg,#2b2424,#8a2a30 55%,#3a2a2a)"></div>
  <div class="photo" role="img" aria-label="Brown and white cows in golden grassland" style="left:270px;top:33px;width:221px;height:328px;background:linear-gradient(180deg,#c9c7a8,#b7a96d 45%,#8f8a4a)"></div>
  <div class="photo" role="img" aria-label="Herd of Holstein cows on a green pasture under blue sky" style="left:516px;top:33px;width:221px;height:328px;background:linear-gradient(180deg,#2a4f9a,#7aa0cf 40%,#4c6b2c 65%,#3d5a22)"></div>
  <div class="photo" role="img" aria-label="Raw meat cuts displayed in a butcher's counter" style="left:764px;top:33px;width:221px;height:328px;background:linear-gradient(160deg,#9a2b30,#c24a4a 50%,#7d2024)"></div>
  <div class="abs" style="left:23px;top:381px;width:221px"><div class="heading">Lorem ipsum is simply<br>dummy text</div><div style="border-top:1px solid var(--rule);margin:8px 0 12px"></div><p class="copy">There are many variations of passages of Lorem Ipsum available, but the majority have suffered alteration in some form, by injected humour, or randomised words which don't look.</p></div>
  <div class="abs" style="left:270px;top:381px;width:221px"><div class="heading">Lorem ipsum is simply<br>dummy text</div><div style="border-top:1px solid var(--rule);margin:8px 0 12px"></div><p class="copy">There are many variations of passages of Lorem Ipsum available, but the majority have suffered alteration in some form, by injected humour, or randomised words which don't look.</p></div>
  <div class="abs" style="left:516px;top:381px;width:221px"><div class="heading">Lorem ipsum is simply<br>dummy text</div><div style="border-top:1px solid var(--rule);margin:8px 0 12px"></div><p class="copy">There are many variations of passages of Lorem Ipsum available, but the majority have suffered alteration in some form, by injected humour, or randomised words which don't look.</p></div>
  <div class="abs" style="left:764px;top:381px;width:221px"><div class="heading">Lorem ipsum is simply<br>dummy text</div><div style="border-top:1px solid var(--rule);margin:8px 0 12px"></div><p class="copy">There are many variations of passages of Lorem Ipsum available, but the majority have suffered alteration in some form, by injected humour, or randomised words which don't look.</p></div>
  <div class="page-no">03</div>
</section>

<!-- 04 -->
<section class="slide light" style="top:2532px">
  <div class="abs" style="left:0;top:0;width:493px;height:100%;background:var(--maroon)"></div>
  <div class="abs" style="left:493px;top:0;right:0;height:100%;background:var(--grey)"></div>

  <div class="photo" role="img" aria-label="Raw steak with garlic" style="left:23px;top:49px;width:160px;height:124px;background:linear-gradient(135deg,#3b2b2b,#b03a40 55%,#5a3a3a)"></div>
  <div class="abs" style="left:206px;top:52px;width:230px"><div class="heading">Lorem ipsum is simply<br>dummy text</div><p class="copy" style="margin-top:6px">There are many variations of passages of Lorem Ipsum available, but the majority have suffered alteration in some form, by injected humour,.</p></div>
  <div class="photo" role="img" aria-label="Butcher cutting a large piece of beef" style="left:23px;top:222px;width:160px;height:124px;background:linear-gradient(135deg,#2e6f76,#b8333a 55%,#3a4a52)"></div>
  <div class="abs" style="left:206px;top:225px;width:230px"><div class="heading">Lorem ipsum is simply<br>dummy text</div><p class="copy" style="margin-top:6px">There are many variations of passages of Lorem Ipsum available, but the majority have suffered alteration in some form, by injected humour,.</p></div>
  <div class="photo" role="img" aria-label="Raw rib steaks on a dark surface" style="left:23px;top:398px;width:160px;height:124px;background:linear-gradient(135deg,#111,#5a1a1e 60%,#2a1a1a)"></div>
  <div class="abs" style="left:206px;top:401px;width:230px"><div class="heading">Lorem ipsum is simply<br>dummy text</div><p class="copy" style="margin-top:6px">There are many variations of passages of Lorem Ipsum available, but the majority have suffered alteration in some form, by injected humour,.</p></div>

  <div class="photo" role="img" aria-label="Cows feeding on hay in a barn" style="left:547px;top:49px;width:160px;height:124px;background:linear-gradient(135deg,#4a3a2a,#a08658 60%,#6a5a40)"></div>
  <div class="abs" style="left:728px;top:52px;width:230px"><div class="heading">Lorem ipsum is simply<br>dummy text</div><p class="copy" style="margin-top:6px">There are many variations of passages of Lorem Ipsum available, but the majority have suffered alteration in some form, by injected humour,.</p></div>
  <div class="photo" role="img" aria-label="Brown cow in a field at sunset" style="left:547px;top:222px;width:160px;height:124px;background:linear-gradient(180deg,#d08a3a,#9a6a2a 50%,#5a4a22)"></div>
  <div class="abs" style="left:728px;top:225px;width:230px"><div class="heading">Lorem ipsum is simply<br>dummy text</div><p class="copy" style="margin-top:6px">There are many variations of passages of Lorem Ipsum available, but the majority have suffered alteration in some form, by injected humour,.</p></div>
  <div class="photo" role="img" aria-label="Cows grazing on green pasture under blue sky" style="left:547px;top:398px;width:160px;height:124px;background:linear-gradient(180deg,#1c4a9a,#6a9ad0 45%,#3f8a2a 60%,#2f6a20)"></div>
  <div class="abs" style="left:728px;top:401px;width:230px"><div class="heading">Lorem ipsum is simply<br>dummy text</div><p class="copy" style="margin-top:6px">There are many variations of passages of Lorem Ipsum available, but the majority have suffered alteration in some form, by injected humour,.</p></div>
  <div class="page-no" style="border:1px solid var(--white)">04</div>
</section>

<!-- 05 -->
<section class="slide" style="top:3135px">
  <div class="abs" style="left:39px;top:130px;width:357px">
    <div class="heading">Lorem ipsum is simply dummy text</div>
    <p class="copy" style="margin-top:4px">There are many variations of passages of Lorem Ipsum available, but the majority have suffered alteration in some form, by injected humour, or randomised words which don't look.</p>
  </div>
  <div class="abs" style="left:39px;top:231px;width:357px;border-top:1px solid var(--rule)"></div>
  <div class="abs" style="left:39px;top:258px;width:357px">
    <div class="heading">Lorem ipsum is simply dummy text</div>
    <p class="copy" style="margin-top:4px">There are many variations of passages of Lorem Ipsum available, but the majority have suffered alteration in some form, by injected humour, or randomised words which don't look.</p>
  </div>
  <div class="abs" style="left:39px;top:359px;width:357px;border-top:1px solid var(--rule)"></div>
  <div class="abs" style="left:39px;top:386px;width:357px">
    <div class="heading">Lorem ipsum is simply dummy text</div>
    <p class="copy" style="margin-top:4px">There are many variations of passages of Lorem Ipsum available, but the majority have suffered alteration in some form, by injected humour, or randomised words which don't look.</p>
  </div>
  <div class="photo" role="img" aria-label="Holstein cow standing in green pasture under deep blue sky" style="left:419px;top:0;right:0;height:100%;background:linear-gradient(180deg,#123a8a 0%,#3f6fc0 45%,#8ab0e0 68%,#4e8a2e 74%,#3a6e22 100%)"></div>
  <div class="page-no">05</div>
</section>

<!-- 06 -->
<section class="slide" style="top:3738px">
  <div class="abs" style="left:0;right:0;top:54px;text-align:center">
    <div style="color:var(--maroon);font-weight:700;font-size:13px">WHAT WE DO</div>
    <div style="color:var(--maroon);font-weight:800;font-size:30px;margin-top:2px">SERVICES FOR YOU</div>
  </div>
  <div class="photo" role="img" aria-label="Brown and white calf under a bright cloudy sky" style="left:35px;top:144px;width:287px;height:285px;box-shadow:0 3px 8px rgba(0,0,0,.35);background:linear-gradient(180deg,#3a74c4,#b8cde6 45%,#8a5a2a 60%,#4f8a2e)"></div>
  <div class="photo" role="img" aria-label="Black and white calves in a barn" style="left:355px;top:144px;width:287px;height:285px;box-shadow:0 3px 8px rgba(0,0,0,.35);background:linear-gradient(180deg,#2a2a2a,#8a8a80 50%,#6a5a3a)"></div>
  <div class="photo" role="img" aria-label="Holstein cow on a pasture at dusk" style="left:675px;top:144px;width:287px;height:285px;box-shadow:0 3px 8px rgba(0,0,0,.35);background:linear-gradient(180deg,#4a5a8a,#7a8aaa 45%,#3a5a2a 70%,#2e4a20)"></div>
  <div class="abs" style="left:35px;top:456px;width:287px;text-align:center"><div class="heading">Veal Entrecote</div><p class="copy" style="margin-top:6px">There are many variations of passages of Lorem Ipsum available, but the majority have suffered alteration in some form, by injected humour, or randomised words which don't.</p></div>
  <div class="abs" style="left:355px;top:456px;width:287px;text-align:center"><div class="heading">Beef Tenderloin</div><p class="copy" style="margin-top:6px">There are many variations of passages of Lorem Ipsum available, but the majority have suffered alteration in some form, by injected humour, or randomised words which don't.</p></div>
  <div class="abs" style="left:675px;top:456px;width:287px;text-align:center"><div class="heading">Beaf Ribs</div><p class="copy" style="margin-top:6px">There are many variations of passages of Lorem Ipsum available, but the majority have suffered alteration in some form, by injected humour, or randomised words which don't.</p></div>
  <div class="page-no">06</div>
</section>

<!-- 07 -->
<section class="slide" style="top:4339px">
  <div class="abs" style="left:47px;top:70px;width:320px">
    <div class="heading">Lorem ipsum is simply dummy text</div>
    <p class="copy" style="margin-top:6px">Lorem ipsum dolor sit amet, consectetur adipiscing elit, sed do eiusmod tempor incididunt ut labore et dolore magna aliqua. Ut enim ad minim veniam, quis nostrud exercitation ullamco laboris nisi ut aliquip ex ea commodo consequat. Duis aute irure dolor in reprehenderit in voluptate velit esse cillum dolore eu fugiat nulla pariatur. Excepteur sint occaecat cupidatat non proident, sunt in culpa qui officia</p>
  </div>
  <div class="photo" role="img" aria-label="Hands in white coat holding raw beef" style="left:402px;top:14px;width:238px;height:233px;background:linear-gradient(135deg,#e6e2de,#b0545a 55%,#d8d2cc)"></div>
  <div class="photo" role="img" aria-label="Cows grazing in a meadow at sunset" style="left:650px;top:10px;width:343px;height:238px;background:linear-gradient(180deg,#2a4a8a,#e0b060 40%,#5a7a2a 60%,#3a5a1e)"></div>
  <div class="photo" role="img" aria-label="Row of Holstein cows standing in a field" style="left:298px;top:256px;width:343px;height:281px;background:linear-gradient(180deg,#7aa0d0,#c8d8e8 35%,#3a3a3a 55%,#5a7a2e)"></div>
  <div class="photo" role="img" aria-label="Butcher in red apron preparing meat at the counter" style="left:650px;top:252px;width:281px;height:235px;background:linear-gradient(135deg,#3a2a22,#c23a30 50%,#6a5a52)"></div>
  <div class="page-no">07</div>
</section>

</body>
</html>
```